Elevating our current Business Card Design

We want to elevate our current business card with a new design to look like a zenith 300 company. We are a premium lubricant distributor (oil and grease).
We need 2 versions, version 1 is as per the uploaded a copy of our current business card with the English version.
For our Chinese version we need to use the front to be English in English and have the back of the card designed exactly like the front for all info to be in Chinese.
The design template needs to be such that we can amend the template with adding different information for each person's card.
The background colour of the card can be changed- we just need to clearly see all information on the card and logos.
The QJR and Ember steady logos cannot have any colour or display changes- only use the logos attached.
All logos need to be included and all information from the attached current card

```html
<!DOCTYPE html>
<html lang="en">
<head>
<meta charset="utf-8">
<title>Kestrel business card</title>
<link rel="stylesheet" href="https://fonts.googleapis.com/css2?family=Open+Sans:wght@400;600;700;800&display=swap">
<style>
  :root {
    --stage: #222222;
    --card-green: #06301f;
    --card-white: #ffffff;
    --brand-red: #e8302a;
    --deep-red: #991b20;
    --accent-orange: #ef7d1a;
    --accent-gold: #d9a22c;
    --badge-grey: #9a9a9a;
    --badge-orange: #f07f1c;
    --text-light: #ffffff;
    --text-dark: #1c1c1c;
  }
  * { box-sizing: border-box; margin: 0; padding: 0; }
  html, body { width: 1200px; height: 780px; overflow: hidden; background: var(--stage); }
  body { font-family: "Open Sans", sans-serif; position: relative; }

  .card {
    position: absolute;
    top: 225px;
    width: 540px;
    height: 330px;
    border-radius: 22px;
    overflow: hidden;
  }
  .card--back { left: 40px; background: var(--card-green); }
  .card--front { left: 620px; background: var(--card-green); }

  .back-mark {
    position: absolute; inset: 0;
    display: flex; align-items: center; justify-content: center; gap: 16px;
  }
  .brand-dot { width: 40px; height: 40px; border-radius: 50%; background: var(--accent-gold); }
  .brand-name {
    font-family: "Open Sans", sans-serif; font-weight: 800;
    font-size: 76px; letter-spacing: 2px; color: var(--brand-red); line-height: 1;
  }

  .front-waves { position: absolute; inset: 0; width: 540px; height: 330px; }

  .front-mark {
    position: absolute; right: 40px; top: 38px;
    display: flex; align-items: center; gap: 10px;
  }
  .front-mark .brand-dot { width: 22px; height: 22px; }
  .front-mark .brand-name { font-size: 46px; }

  .person { position: absolute; left: 26px; top: 120px; }
  .person-name { font-weight: 700; font-size: 30px; color: var(--brand-red); line-height: 1.05; }
  .person-role { font-weight: 600; font-size: 13px; color: var(--text-dark); margin-top: 2px; }

  .contact { position: absolute; left: 40px; top: 222px; color: var(--text-light); font-size: 12.5px; line-height: 1.35; }
  .address { margin-bottom: 8px; }
  .contact-list { list-style: none; }
  .contact-list li { display: flex; align-items: center; gap: 8px; }
  .contact-list svg { width: 12px; height: 12px; flex: none; }

  .credentials { position: absolute; right: 18px; bottom: 20px; width: 230px; height: 110px; }
  .cert-row { position: absolute; right: 6px; top: 0; display: flex; gap: 14px; }
  .cert-badge { width: 34px; height: 34px; border-radius: 50%; background: var(--badge-orange); border: 4px solid var(--badge-grey); }
  .member-badge { position: absolute; left: 0; top: 34px; width: 46px; height: 30px; border-radius: 6px; background: var(--card-white); }
  .partner-strip {
    position: absolute; left: 2px; bottom: 0; width: 226px; height: 34px;
    display: flex; border: 2px solid var(--brand-red);
  }
  .partner-client {
    flex: 1.2; background: var(--card-white);
    display: flex; align-items: center; gap: 5px; padding-left: 8px;
  }
  .partner-client .brand-name { font-size: 15px; letter-spacing: 0; }
  .partner-client .descriptor { font-size: 6.5px; font-weight: 600; color: var(--brand-red); line-height: 1.1; text-transform: uppercase; }
  .partner-supplier {
    flex: 1; background: var(--brand-red);
    display: flex; align-items: center; justify-content: center;
    font-weight: 800; font-size: 15px; color: var(--text-light);
  }
</style>
</head>
<body>

<section class="card card--back" aria-label="Card back">
  <div class="back-mark">
    <span class="brand-dot"></span>
    <span class="brand-name">Kestrel</span>
  </div>
</section>

<section class="card card--front" aria-label="Card front">
  <svg class="front-waves" viewBox="0 0 540 330" aria-hidden="true">
    <path d="M0 0 H540 V90 C500 160 420 170 320 172 C200 175 90 185 0 225 Z" fill="var(--card-white)"/>
    <path d="M540 90 C500 160 420 170 320 172 C200 175 90 185 0 225 V236 C90 196 200 188 320 186 C430 184 510 165 540 110 Z" fill="var(--deep-red)"/>
    <path d="M300 162 C420 158 500 140 530 80" stroke="var(--accent-gold)" stroke-width="4" fill="none"/>
    <path d="M0 222 C60 196 120 186 200 180" stroke="var(--accent-orange)" stroke-width="5" fill="none"/>
  </svg>

  <div class="front-mark">
    <span class="brand-dot"></span>
    <span class="brand-name">Kestrel</span>
  </div>

  <div class="person">
    <p class="person-name">Maren Holt</p>
    <p class="person-role">Administration Executive</p>
  </div>

  <div class="contact">
    <p class="address">48 Depot Crescent<br>Harlow, WA 6199</p>
    <ul class="contact-list">
      <li><svg viewBox="0 0 12 12"><path d="M2 1 L4.5 1 L5.5 3.5 L4 4.5 C4.7 6 6 7.3 7.5 8 L8.5 6.5 L11 7.5 V10 C6 10.5 1.5 6 2 1 Z" fill="var(--brand-red)"/></svg>1300 246 810</li>
      <li><svg viewBox="0 0 12 12"><rect x="3" y="0.5" width="6" height="11" rx="1.2" fill="none" stroke="var(--brand-red)" stroke-width="1.2"/></svg>+61 400 127 365</li>
      <li><svg viewBox="0 0 12 12"><rect x="1" y="4" width="10" height="7" rx="1" fill="var(--brand-red)"/><rect x="3" y="1" width="6" height="3" fill="var(--brand-red)"/></svg>+61 8 9002 4417</li>
      <li><svg viewBox="0 0 12 12"><circle cx="6" cy="6" r="5.2" fill="var(--brand-red)"/><path d="M1 6 H11 M6 1 V11" stroke="var(--card-green)" stroke-width="0.8"/></svg>www.kestreldirect.com</li>
      <li><svg viewBox="0 0 12 12"><rect x="1" y="2.5" width="10" height="7.5" rx="1" fill="var(--brand-red)"/><path d="M1.5 3 L6 7 L10.5 3" stroke="var(--card-green)" stroke-width="0.9" fill="none"/></svg>maren.holt@kestreldirect.com</li>
    </ul>
  </div>

  <div class="credentials">
    <div class="cert-row">
      <span class="cert-badge" role="img" aria-label="QJR certification badge"></span>
      <span class="cert-badge" role="img" aria-label="QJR certification badge"></span>
      <span class="cert-badge" role="img" aria-label="QJR certification badge"></span>
    </div>
    <span class="member-badge" role="img" aria-label="Ember steady network member badge"></span>
    <div class="partner-strip">
      <div class="partner-client">
        <span class="brand-name">Kestrel</span>
        <span class="descriptor">Kestrel<br>Lubricant<br>Distributors</span>
      </div>
      <div class="partner-supplier">Norvane</div>
    </div>
  </div>
</section>

</body>
</html>
```